Marwick Law Letterhead

We need a new letterhead design for a Law Firm. The address for the law firm is 1475 Calloway Street, Suite 210, Houston, Texas 77041. Phone Number: 832-361-9027; Fax Number: 832-614-7359. The logo is uploaded to the project.

```html
<!DOCTYPE html>
<html lang="en">
<head>
<meta charset="utf-8">
<title>Marwick Law Letterhead</title>
<link rel="stylesheet" href="https://fonts.googleapis.com/css2?family=Roboto:wght@400;500&display=swap">
<style>
  :root {
    --backdrop: #dedede;
    --paper: #f1f1f1;
    --navy: #1b2a57;
    --navy-deep: #15224a;
    --red: #c8202a;
    --ink: #3a3a3a;
    --signature-tone: #d9d9d9;
  }
  * { box-sizing: border-box; margin: 0; padding: 0; }
  html, body {
    width: 1069px;
    height: 1200px;
    overflow: hidden;
    background: var(--backdrop);
    font-family: "Roboto", Arial, sans-serif;
  }
  .letterhead {
    position: absolute;
    left: 131px;
    top: 30px;
    width: 807px;
    height: 1140px;
    background: var(--paper);
    box-shadow: 0 6px 22px rgba(0,0,0,0.12);
    color: var(--ink);
  }
  .brand {
    position: absolute;
    left: 47px;
    top: 68px;
    display: flex;
    align-items: center;
    gap: 12px;
  }
  .brand-mark {
    width: 26px;
    height: 26px;
    background: var(--navy);
  }
  .brand-name {
    font-size: 40px;
    font-weight: 500;
    color: var(--navy);
    letter-spacing: 0.5px;
    line-height: 1;
  }
  .recipient {
    position: absolute;
    left: 47px;
    top: 324px;
    font-size: 14.6px;
    line-height: 23px;
    font-style: normal;
  }
  .letter-body {
    position: absolute;
    left: 47px;
    top: 433px;
    width: 713px;
    font-size: 14.6px;
    line-height: 23px;
  }
  .letter-body p { margin-bottom: 21px; }
  .letter-body p.gap-large { margin-bottom: 25px; }
  .line {
    display: block;
    white-space: nowrap;
    text-align: justify;
    text-align-last: justify;
  }
  .line.last { text-align-last: left; }
  .closing {
    position: absolute;
    left: 47px;
    top: 816px;
    font-size: 14.6px;
    line-height: 23px;
  }
  .signature {
    position: absolute;
    left: 49px;
    top: 855px;
    width: 146px;
    height: 60px;
    background: linear-gradient(90deg, var(--signature-tone), #e6e6e6);
    border-radius: 4px;
  }
  .footer-rule {
    position: absolute;
    left: 0;
    top: 1076px;
    width: 100%;
    height: 5px;
    background: linear-gradient(90deg, #8e1a22, var(--red));
  }
  .footer-band {
    position: absolute;
    left: 0;
    top: 1081px;
    width: 100%;
    height: 59px;
    background: linear-gradient(90deg, var(--navy-deep), var(--navy));
    display: flex;
    align-items: center;
    padding-left: 52px;
    gap: 15px;
    color: #ffffff;
    font-size: 16px;
  }
  .contact-item { display: flex; align-items: center; gap: 5px; white-space: nowrap; }
  .contact-icon { width: 13px; height: 13px; fill: var(--red); }
</style>
</head>
<body>
  <main class="letterhead">
    <header class="brand">
      <span class="brand-mark"></span>
      <span class="brand-name">Marwick Law</span>
    </header>

    <address class="recipient">
      Mr/s<br>
      First Name and Last Name<br>
      Company Name<br>
      Address
    </address>

    <section class="letter-body">
      <p class="gap-large">
        <span class="line">Lorem Ipsum is simply dummy text of the printing and typesetting industry. Lorem Ipsum has been the</span>
        <span class="line">industry's standard dummy text ever since the 1500s, when an unknown printer took a galley of type</span>
        <span class="line">and scrambled it to make a type specimen book. It has survived not only five centuries, but also the leap</span>
        <span class="line">into electronic typesetting, remaining essentially unchanged. It was popularised in the 1960s with the</span>
        <span class="line last">release of Typeline sheets containing Lorem Ipsum passages.</span>
      </p>
      <p>
        <span class="line">he standard chunk of Lorem Ipsum used since the 1500s is reproduced below for those interested. Sec-</span>
        <span class="line">tions 1.10.32 and 1.10.33 from "de Ordine Verborum et Litterarum" by Vareno are also reproduced in their</span>
        <span class="line">exact original form, accompanied by English versions from the 1914 translation by H. Brackley. Lorem</span>
        <span class="line">ipsum dolor sit amet, consectetur adipiscing elit, sed do eiusmod tempor incididunt ut labore et dolore</span>
        <span class="line last">magna aliqua.</span>
      </p>
      <p>
        <span class="line">It is a long established fact that a reader will be distracted by the readable content of a page when look-</span>
        <span class="line">ing at its layout. The point of using Lorem Ipsum is that it has a more-or-less normal distribution of</span>
        <span class="line">letters, as opposed to using 'Content here, content here', making it look like readable English. Many</span>
        <span class="line last">desktop publishing packages and web page editors now .</span>
      </p>
    </section>

    <p class="closing">Your Sincerely,</p>
    <div class="signature" role="img" aria-label="Handwritten signature"></div>

    <div class="footer-rule"></div>
    <footer class="footer-band">
      <span class="contact-item">
        <svg class="contact-icon" viewBox="0 0 16 16" aria-hidden="true"><path d="M2 6c0-2 2-3 6-3s6 1 6 3v1h-3V5.5C10 5 9 5 8 5s-2 0-3 .5V7H2z"/><path d="M4 8h8l2 5H2z"/></svg>
        832-361-9027
      </span>
      <span class="contact-item">
        <svg class="contact-icon" viewBox="0 0 16 16" aria-hidden="true"><rect x="4" y="1" width="8" height="4"/><rect x="1" y="6" width="14" height="6" rx="1"/><rect x="4" y="10" width="8" height="5" fill="#f3b5b8"/></svg>
        832-614-7359
      </span>
      <span class="contact-item">
        <svg class="contact-icon" viewBox="0 0 16 16" aria-hidden="true"><path d="M8 0a5.5 5.5 0 0 0-5.5 5.5C2.5 10 8 16 8 16s5.5-6 5.5-10.5A5.5 5.5 0 0 0 8 0zm0 8a2.5 2.5 0 1 1 0-5 2.5 2.5 0 0 1 0 5z"/></svg>
        1475 Calloway Street Suite 210, Houston, Texas 77041
      </span>
    </footer>
  </main>
</body>
</html>
```